Real estate broker business card

Want a modern celan but effective business card for my residential and commercial real estate business. I want the back of the card to advertise my services and to capture business. I have attached the back of my current business card fore ideas
Updates

Logos, photo and text updates added! Added Saturday, September 3, 2016

Project Deadline Extended Reason: LOGOS, PHOTOS AND TEST JUST UPLOADED! I'M READY TO PICK A DESIGN! THANK YOU! Added Saturday, September 3, 2016

Target Market(s)

home buyers and seller. commercial buyers and sellers

Industry/Entity Type

Real Estate

Contact Information for Business Card

must have my contact information and my photo

Requirements
Must have
• Carla Ventrino
• Owner & Qualifying Broker
• Ventrino Real Estate Services
• 505.718.2094
• carla@ventrinohomes.example
• www.ventrinohomes.example
Nice to have
• metallic
• Business capture text: " Don't buy or lease property without someone looking out for your best interests. I will represent you on your home or investment purchase for FREE!"
• "Home owners, call today to receive a FREE market analysis for your homes value!

```html
<!DOCTYPE html>
<html lang="en">
<head>
<meta charset="utf-8">
<title>Ventrino Real Estate Services – Business Card</title>
<link rel="stylesheet" href="https://fonts.googleapis.com/css2?family=Source+Sans+3:ital,wght@0,400;0,600;0,700;1,400&display=swap">
<style>
  :root {
    --teal-deep: #0b5a68;
    --teal-mid: #0f6f7e;
    --teal-soft: #17808f;
    --teal-ink: #0c5f6d;
    --silver: #d3dbde;
    --grey-text: #666d70;
    --white: #ffffff;
    --stage: #eceff0;
    --photo-dark: #3a2a24;
    --photo-light: #e9e4e1;
  }
  * { box-sizing: border-box; margin: 0; padding: 0; }
  html, body {
    width: 1200px; height: 900px; overflow: hidden;
    background: var(--stage);
    font-family: "Source Sans 3", Arial, sans-serif;
  }
  .canvas { position: relative; width: 1200px; height: 900px; }

  .card {
    position: absolute; overflow: hidden;
    box-shadow: 0 6px 18px rgba(0,0,0,.18);
  }

  /* Front */
  .card-front {
    left: 238px; top: 60px; width: 555px; height: 345px;
    background: linear-gradient(135deg, var(--teal-mid), var(--teal-deep));
    color: var(--white);
  }
  .brand {
    position: absolute; display: flex; align-items: center; gap: 10px;
  }
  .brand-mark { width: 14px; height: 14px; flex: none; }
  .brand-name { font-weight: 600; line-height: 1; }
  .brand-name .brand-main { display: block; letter-spacing: .04em; text-transform: uppercase; }
  .brand-name .brand-sub { display: block; letter-spacing: .22em; text-transform: uppercase; margin-top: 4px; }

  .card-front .brand { left: 47px; top: 58px; }
  .card-front .brand-mark { background: var(--silver); }
  .card-front .brand-name { color: var(--silver); }
  .card-front .brand-main { font-size: 30px; }
  .card-front .brand-sub { font-size: 10px; }

  .front-accent {
    position: absolute; left: 340px; top: 30px; width: 320px; height: 320px;
    border-radius: 50%;
    background: var(--teal-soft);
    border: 10px solid var(--white);
  }

  .person { position: absolute; left: 45px; top: 166px; }
  .person-name { font-size: 18px; font-weight: 700; }
  .person-title { font-size: 14.5px; margin-top: 1px; }

  .contacts { position: absolute; left: 45px; top: 244px; list-style: none; }
  .contacts li {
    display: flex; align-items: center; gap: 8px;
    font-size: 14.5px; height: 20px;
  }
  .contacts svg { width: 11px; height: 11px; fill: var(--white); flex: none; }

  /* Back */
  .card-back {
    left: 457px; top: 518px; width: 560px; height: 344px;
    background: var(--white);
  }
  .card-back .brand { left: 34px; top: 42px; gap: 12px; }
  .card-back .brand-mark { width: 18px; height: 18px; background: var(--teal-ink); }
  .card-back .brand-name { color: var(--teal-ink); }
  .card-back .brand-main { font-size: 40px; }
  .card-back .brand-sub { font-size: 13px; margin-top: 6px; }

  .pitch {
    position: absolute; left: 33px; top: 163px; width: 330px;
    font-size: 15px; line-height: 20px; color: var(--teal-ink);
  }
  .offer {
    position: absolute; left: 33px; top: 260px; width: 320px;
    font-size: 14px; line-height: 20px; font-style: italic; color: var(--grey-text);
  }
  .portrait {
    position: absolute; left: 378px; top: 66px; width: 182px; height: 278px;
    border-radius: 90px 90px 0 0;
    background: linear-gradient(180deg, var(--photo-dark) 0%, #7a5a4c 45%, var(--photo-light) 100%);
  }
</style>
</head>
<body>
<main class="canvas">

  <section class="card card-front">
    <div class="front-accent" aria-hidden="true"></div>
    <div class="brand">
      <span class="brand-mark"></span>
      <span class="brand-name"><span class="brand-main">Ventrino</span><span class="brand-sub">Real Estate Services</span></span>
    </div>
    <div class="person">
      <p class="person-name">Carla Ventrino</p>
      <p class="person-title">Owner &amp; Qualifying Broker</p>
    </div>
    <ul class="contacts">
      <li><svg viewBox="0 0 24 24"><path d="M6.6 10.8a15 15 0 0 0 6.6 6.6l2.2-2.2a1 1 0 0 1 1-.25 11.4 11.4 0 0 0 3.6.57 1 1 0 0 1 1 1V20a1 1 0 0 1-1 1A17 17 0 0 1 3 4a1 1 0 0 1 1-1h3.5a1 1 0 0 1 1 1c0 1.25.2 2.45.57 3.57a1 1 0 0 1-.25 1z"/></svg>505.718.2094</li>
      <li><svg viewBox="0 0 24 24"><path d="M2 5h20v14H2z M3 6l9 7 9-7" fill="none" stroke="#fff" stroke-width="0"/><path d="M2 5h20v2l-10 7L2 7zM2 9l10 7 10-7v10H2z"/></svg>carla@ventrinohomes.example</li>
      <li><svg viewBox="0 0 24 24"><circle cx="12" cy="12" r="10"/><path d="M2 12h20M12 2c3 3 3 17 0 20M12 2c-3 3-3 17 0 20" stroke="#0b5a68" stroke-width="1.6" fill="none"/></svg>www.ventrinohomes.example</li>
    </ul>
  </section>

  <section class="card card-back">
    <div class="brand">
      <span class="brand-mark"></span>
      <span class="brand-name"><span class="brand-main">Ventrino</span><span class="brand-sub">Real Estate Services</span></span>
    </div>
    <p class="pitch">Don't buy or lease property without someone looking out for your best interests. I will represent you on your home or investment purchase for FREE!</p>
    <p class="offer">Home owners, call today to receive a FREE market analysis for your homes value!</p>
    <div class="portrait" role="img" aria-label="Portrait photo of Carla Ventrino"></div>
  </section>

</main>
</body>
</html>
```